Heron Loan Partners Business Card

We need a business card design for our mortgage servicing company. In addition to servicing the loans of homeowners, we help homeowners with purchasing their homes and any mortgage refinancing. We would like to see designs that use the colors in the logo attached below (gold-ish yellow and navy blue), and any other design you deem fit! The design should communicate a simpler life with smart mortgages provided by Heron.

```html
<!DOCTYPE html>
<html lang="en">
<head>
<meta charset="utf-8">
<title>Heron Loan Partners Business Card</title>
<link href="https://fonts.googleapis.com/css2?family=Open+Sans:wght@400;600;700&display=swap" rel="stylesheet">
<style>
  :root {
    --gold: #e0ac33;
    --navy: #221f56;
    --ink: #1c1c1c;
    --paper: #ffffff;
    --backdrop: #2b2e33;
  }
  * { margin: 0; padding: 0; box-sizing: border-box; }
  html, body { width: 1200px; height: 780px; overflow: hidden; }
  body {
    background: var(--backdrop);
    font-family: "Open Sans", sans-serif;
    position: relative;
  }
  .card {
    position: absolute;
    top: 235px;
    width: 540px;
    height: 309px;
    background: var(--paper);
    border-radius: 18px;
    overflow: hidden;
  }
  .card--front { left: 40px; }
  .card--back { left: 620px; }

  .brand-name {
    position: absolute;
    font-weight: 700;
    color: var(--gold);
    white-space: nowrap;
  }
  .card--front .brand-name { left: 48px; top: 52px; font-size: 24px; }
  .card--back .brand-name {
    left: 0; right: 0; top: 128px;
    text-align: center; font-size: 36px;
  }

  .divider {
    position: absolute;
    left: 120px; top: 168px;
    width: 372px; height: 1.5px;
    background: var(--ink);
  }
  .accent-tab {
    position: absolute;
    right: 0; top: 150px;
    width: 48px; height: 38px;
    background: var(--gold);
  }

  .person { position: absolute; right: 56px; top: 100px; text-align: right; }
  .person-name { font-size: 28px; font-weight: 700; line-height: 1; }
  .person-name .first { color: var(--gold); }
  .person-name .last { color: var(--navy); }
  .person-title { font-size: 15px; color: var(--ink); margin-top: 6px; letter-spacing: 0.3px; }

  .contacts { position: absolute; left: 26px; top: 196px; list-style: none; }
  .contacts li {
    display: flex; align-items: center; gap: 7px;
    font-size: 13px; color: var(--ink); line-height: 20px;
  }
  .contacts svg { width: 11px; height: 11px; flex: none; }

  .address {
    position: absolute; right: 110px; top: 204px;
    font-size: 15px; line-height: 22px; color: var(--ink); text-align: right;
    font-style: normal;
  }
</style>
</head>
<body>
  <section class="card card--front" aria-label="Card front">
    <div class="brand-name">Heron Loan Partners</div>

    <div class="person">
      <div class="person-name"><span class="first">Lena</span> <span class="last">Marsh</span></div>
      <div class="person-title">Managing Director</div>
    </div>

    <div class="divider"></div>
    <div class="accent-tab"></div>

    <ul class="contacts">
      <li>
        <svg viewBox="0 0 12 12"><path d="M2.5 1 L4.6 1 L5.3 3.6 L4 4.6 Q5 7 7.4 8 L8.4 6.7 L11 7.4 L11 9.5 Q11 11 9.5 11 Q1 10.5 1 2.5 Q1 1 2.5 1 Z" fill="var(--gold)"/></svg>
        (555) 014-2290
      </li>
      <li>
        <svg viewBox="0 0 12 12"><rect x="0.5" y="2" width="11" height="8" rx="1" fill="var(--gold)"/><path d="M1 2.5 L6 6.5 L11 2.5" stroke="#fff" stroke-width="1" fill="none"/></svg>
        info@heronloan.com
      </li>
      <li>
        <svg viewBox="0 0 12 12"><circle cx="6" cy="6" r="5.5" fill="var(--gold)"/><path d="M0.5 6 H11.5 M6 0.5 Q3 6 6 11.5 M6 0.5 Q9 6 6 11.5" stroke="#fff" stroke-width="0.8" fill="none"/></svg>
        www.heronloan.com
      </li>
    </ul>

    <address class="address">
      480 Lakeside Ave. Suite 310<br>
      Brookfield, TX 75010
    </address>
  </section>

  <section class="card card--back" aria-label="Card back">
    <div class="brand-name">Heron Loan Partners</div>
  </section>
</body>
</html>
```